Business cards and stationary design

We just completed the design of our new logo and we need to print new business cards and letterhead for our nonprofit. We are looking for a fresh new design that shows off our new logo. On letterhead, we must have a column on the right or left to include our Board of Directors (up to 45 names) (see attachment)

Industry/Entity Type

Non-Profit

Contact Information for Business Card

Standard business card with name, title, Company name, mailing address phone numbers, email address and website. Tagline on back "Bringing the homeless home"

Font styles to use
Sans Serif

Requirements
Must have
• include pertinent information above
• new logo
• fonts compatible with logo
• should use logo colors only
Nice to have
• tag lines

```html
<!DOCTYPE html>
<html lang="en">
<head>
<meta charset="utf-8">
<title>Homeward Haven Center – Business Card</title>
<link rel="stylesheet" href="https://fonts.googleapis.com/css2?family=Exo+2:wght@500;600;700&family=Roboto+Condensed:wght@700&display=swap">
<style>
  :root {
    --backdrop: #2b2b2b;
    --brand-red: #d62027;
    --brand-teal: #0083a6;
    --brand-yellow: #fbbc1e;
    --card-light: #f2f2f2;
    --ink-grey: #4f4f4f;
    --white: #ffffff;
  }
  * { margin: 0; padding: 0; box-sizing: border-box; }
  html, body {
    width: 1200px; height: 960px; overflow: hidden;
    background: var(--backdrop);
    font-family: "Exo 2", sans-serif;
  }
  .canvas { position: relative; width: 1200px; height: 960px; }

  .card {
    position: absolute; left: 320px; width: 600px; height: 342px; overflow: hidden;
  }

  /* Back of card */
  .card-back { top: 108px; background: var(--brand-red); }
  .card-back .org-name {
    position: absolute; left: 0; right: 0; top: 148px;
    text-align: center; color: var(--white);
    font-weight: 700; font-size: 30px; letter-spacing: 2px; text-transform: uppercase;
  }
  .card-back .website {
    position: absolute; left: 0; right: 0; top: 290px;
    text-align: center; color: var(--white);
    font-weight: 500; font-size: 14px; letter-spacing: 4.6px;
  }

  /* Front of card */
  .card-front { top: 493px; background: var(--card-light); }
  .card-front .roof { position: absolute; inset: 0; }
  .holder {
    position: absolute; right: 34px; top: 28px; text-align: right; color: var(--white);
    font-family: "Roboto Condensed", sans-serif; font-weight: 700;
  }
  .holder-name { font-size: 23px; line-height: 1.1; }
  .holder-title { font-size: 15px; margin-top: 4px; }

  .org-mark {
    position: absolute; left: 34px; top: 188px;
    display: flex; align-items: center; gap: 8px;
    color: var(--brand-teal); font-weight: 600; font-size: 20px; letter-spacing: 2px;
    text-transform: uppercase;
  }
  .org-mark .dot { width: 12px; height: 12px; border-radius: 50%; background: var(--brand-teal); }

  .contact-list {
    position: absolute; left: 30px; top: 259px; list-style: none;
    color: var(--ink-grey); font-weight: 600; font-size: 13.5px;
  }
  .contact-list li { display: flex; align-items: center; gap: 8px; height: 19px; }
  .contact-list svg { width: 13px; height: 13px; fill: var(--brand-teal); }

  .mailing-address {
    position: absolute; right: 30px; top: 259px; text-align: right;
    color: var(--ink-grey); font-weight: 600; font-size: 13.5px; line-height: 19px;
    font-style: normal;
  }
</style>
</head>
<body>
<main class="canvas">

  <section class="card card-back">
    <div class="org-name">Homeward Haven</div>
    <div class="website">www.homewardhaven.org</div>
  </section>

  <section class="card card-front">
    <svg class="roof" width="600" height="342" viewBox="0 0 600 342" aria-hidden="true">
      <rect width="600" height="342" fill="var(--brand-teal)"/>
      <polygon points="0,130 278,42 600,142 600,342 0,342" fill="var(--card-light)"/>
      <polyline points="0,133 278,45 600,145" fill="none" stroke="var(--brand-yellow)" stroke-width="6"/>
      <polyline points="0,127 278,39 600,139" fill="none" stroke="var(--white)" stroke-width="1.5"/>
    </svg>

    <div class="holder">
      <div class="holder-name">DANIEL MOREAU</div>
      <div class="holder-title">CEO/FOUNDER</div>
    </div>

    <div class="org-mark"><span class="dot"></span>Homeward Haven Center</div>

    <ul class="contact-list">
      <li>
        <svg viewBox="0 0 24 24"><path d="M6.6 10.8a15.1 15.1 0 0 0 6.6 6.6l2.2-2.2c.3-.3.7-.4 1-.2 1.1.4 2.3.6 3.6.6.6 0 1 .4 1 1V20c0 .6-.4 1-1 1A17 17 0 0 1 3 4c0-.6.4-1 1-1h3.5c.6 0 1 .4 1 1 0 1.3.2 2.5.6 3.6.1.3 0 .7-.2 1z"/></svg>
        512 864 3917
      </li>
      <li>
        <svg viewBox="0 0 24 24"><path d="M2 5h20v14H2z M3 6l9 7 9-7" fill="var(--brand-teal)"/><path d="M3 6.5l9 6.5 9-6.5" fill="none" stroke="var(--card-light)" stroke-width="1.6"/></svg>
        daniel@homewardhaven.org
      </li>
      <li>
        <svg viewBox="0 0 24 24"><circle cx="12" cy="12" r="10"/><path d="M2 12h20M12 2c3 3 3 17 0 20M12 2c-3 3-3 17 0 20" fill="none" stroke="var(--card-light)" stroke-width="1.4"/></svg>
        www.homewardhaven.org
      </li>
    </ul>

    <address class="mailing-address">
      Homeward Haven Center<br>
      2214 Birchwood Road<br>
      Juneau, Alaska 99801
    </address>
  </section>

</main>
</body>
</html>
```